Business Card Design (NEW FILES)

ATTENTION: New vector files are available. Please update your design to reflect/use the new (better resolution) logo images.

Seeking a unique and professional business card design for a commercial drone photography/videography business. The layout should feature
the logo (attached) and include the following information:
Owen Tarrick
614-502-7738
www.skylarkreelworks.example
NRD Certified Remote Pilot

Owen Tarrick

```html
<!DOCTYPE html>
<html lang="en">
<head>
<meta charset="utf-8">
<title>Skylark Reelworks – Business Card</title>
<link rel="stylesheet" href="https://fonts.googleapis.com/css2?family=Poppins:wght@400;500&display=swap">
<style>
  :root {
    --backdrop: #ababab;
    --navy: #131a47;
    --orange: #ef8e58;
    --white: #ffffff;
    --ink: #1b1f33;
  }
  * { box-sizing: border-box; margin: 0; padding: 0; }
  html, body { width: 1093px; height: 1200px; overflow: hidden; }
  body {
    background: var(--backdrop);
    font-family: "Poppins", sans-serif;
    position: relative;
  }
  .card {
    position: absolute;
    left: 265px;
    width: 578px;
    height: 357px;
    border-radius: 24px;
    overflow: hidden;
  }
  .card--front { top: 226px; background: var(--white); }
  .card--back { top: 621px; background: var(--navy); }

  /* brand name */
  .brand {
    position: absolute;
    left: 0; right: 0;
    display: flex;
    align-items: center;
    justify-content: center;
    gap: 14px;
    font-weight: 500;
    letter-spacing: 0.04em;
    text-transform: uppercase;
    white-space: nowrap;
  }
  .brand__dot { border-radius: 50%; flex: none; }
  .card--front .brand { top: 140px; color: var(--navy); font-size: 30px; }
  .card--front .brand__dot { width: 34px; height: 34px; background: var(--navy); }

  /* front info row */
  .info-row {
    position: absolute;
    left: 20px; right: 20px;
    top: 270px;
    display: flex;
    justify-content: center;
    align-items: center;
    gap: 16px;
    white-space: nowrap;
  }
  .identity { text-align: right; }
  .identity__name {
    color: var(--navy);
    font-weight: 500;
    font-size: 24px;
    line-height: 1.05;
    letter-spacing: 0.01em;
    text-transform: uppercase;
  }
  .identity__role {
    color: var(--orange);
    font-size: 15px;
    line-height: 1.2;
    text-transform: uppercase;
  }
  .divider {
    width: 1px;
    height: 40px;
    background: var(--orange);
    flex: none;
  }
  .contact {
    list-style: none;
    color: var(--ink);
    font-size: 16px;
    line-height: 21px;
  }
  .contact li { display: flex; align-items: center; gap: 10px; }
  .contact svg { width: 14px; height: 14px; flex: none; }

  .base-band {
    position: absolute;
    left: 0; right: 0; bottom: 0;
    height: 18px;
    background: var(--navy);
  }
  .base-notch {
    position: absolute;
    left: 275px;
    bottom: 10px;
    width: 28px;
    height: 28px;
    border-radius: 50%;
    background: var(--white);
  }

  /* back */
  .card--back .brand { top: 152px; color: var(--white); font-size: 34px; }
  .card--back .brand__dot { width: 38px; height: 38px; background: var(--white); }
  .credentials {
    position: absolute;
    left: 0; right: 0;
    top: 290px;
    text-align: center;
    font-size: 17px;
    line-height: 21px;
  }
  .credentials__cert { color: var(--white); }
  .credentials__insured { color: var(--orange); }
</style>
</head>
<body>
  <section class="card card--front" aria-label="Card front">
    <div class="brand"><span class="brand__dot"></span><span>Skylark Reelworks</span></div>

    <div class="info-row">
      <div class="identity">
        <p class="identity__name">Owen Tarrick</p>
        <p class="identity__role">Owner</p>
      </div>
      <span class="divider"></span>
      <ul class="contact">
        <li>
          <svg viewBox="0 0 24 24" aria-hidden="true"><path fill="none" stroke="#131a47" stroke-width="2.4" stroke-linejoin="round" d="M6 2.5l3.5 4-2 2.5c1.3 2.8 3.7 5.2 6.5 6.5l2.5-2 4 3.5-2.2 3.2C10 20 4 14 2.8 4.7z"/></svg>
          <span>614-502-7738</span>
        </li>
        <li>
          <svg viewBox="0 0 24 24" aria-hidden="true"><g fill="none" stroke="#131a47" stroke-width="2"><circle cx="12" cy="12" r="10"/><ellipse cx="12" cy="12" rx="4.5" ry="10"/><path d="M2 12h20M4 6.5h16M4 17.5h16"/></g></svg>
          <span>www.skylarkreelworks.example</span>
        </li>
      </ul>
    </div>

    <div class="base-band"></div>
    <div class="base-notch"></div>
  </section>

  <section class="card card--back" aria-label="Card back">
    <div class="brand"><span class="brand__dot"></span><span>Skylark Reelworks</span></div>
    <div class="credentials">
      <p class="credentials__cert">NRD Certified Remote Pilot</p>
      <p class="credentials__insured">Fully Insured</p>
    </div>
  </section>
</body>
</html>
```